New startup requiring business card

New company needed a business card / logo. Company name is
Brindex
Company is providing IT software sales, partnering and consulting services across the APAC region. Catch line is "growing together".
We currently have a feeling yellow as the primary colour given its meaning across the region but open to ideas. Main brief is we want something smart, clean and professional while still leveraging the strength of the name.
A major part of the business is mutually beneficial partnerships, not sure if this helps but maybe visual around linkages between objects.
Also wanting a standard size card, preference is something that will have a D/S cello sheen finish in a matt. But again open to ideas, wow us!
Industry/Entity Type
Software
Font styles to use
Look and feel

```html
<!DOCTYPE html>
<html lang="en">
<head>
<meta charset="utf-8">
<title>Brindex Business Card</title>
<link rel="stylesheet" href="https://fonts.googleapis.com/css2?family=Roboto:wght@300;400;700&display=swap">
<style>
  :root {
    --page-bg: #2b2b2b;
    --card-white: #f1f1f1;
    --stripe-grey: #c4c4c4;
    --stripe-light: #dcdcdc;
    --ink: #1e1e1e;
    --ink-soft: #555555;
    --brand-yellow: #f5ec2e;
    --yellow-glow: #f7f4d2;
  }
  * { box-sizing: border-box; margin: 0; padding: 0; }
  html, body {
    width: 1200px; height: 646px; overflow: hidden;
    background: var(--page-bg);
    font-family: "Roboto", Arial, sans-serif;
  }
  .stage { position: relative; width: 1200px; height: 646px; }
  .card {
    position: absolute; top: 180px;
    width: 500px; height: 286px;
    overflow: hidden;
    box-shadow: 0 10px 30px rgba(0,0,0,.45);
  }
  /* Front */
  .card-front { left: 60px; background: var(--card-white); }
  .front-edge {
    position: absolute; left: 0; top: 0; width: 34px; height: 100%;
    background: var(--stripe-grey);
  }
  .front-edge-light {
    position: absolute; left: 34px; top: 0; width: 22px; height: 100%;
    background: var(--stripe-light);
  }
  .edge-accent {
    position: absolute; left: 0; top: 196px; width: 56px; height: 26px;
    background: var(--brand-yellow);
  }
  .corner-tab {
    position: absolute; right: 0; top: 0; width: 24px; height: 24px;
    background: var(--stripe-light);
  }
  .holder { position: absolute; right: 28px; top: 28px; text-align: right; }
  .holder-name { font-weight: 700; font-size: 22px; color: var(--ink); letter-spacing: .5px; }
  .holder-role { font-weight: 300; font-size: 9px; color: var(--ink-soft); }
  .front-band {
    position: absolute; right: 0; top: 84px; width: 250px; height: 30px;
    background: var(--brand-yellow);
  }
  .front-brand {
    position: absolute; left: 76px; top: 130px;
    display: flex; align-items: center; gap: 10px;
  }
  .brand-square { width: 34px; height: 34px; background: var(--brand-yellow); }
  .brand-name { font-weight: 700; font-size: 30px; color: var(--ink); letter-spacing: 1px; }
  .contact {
    position: absolute; left: 76px; top: 182px;
    display: grid; grid-template-columns: 62px auto; row-gap: 5px;
    font-size: 11px; font-weight: 400; color: var(--ink-soft);
  }
  /* Back */
  .card-back {
    left: 640px;
    background: radial-gradient(ellipse at 50% 48%, var(--yellow-glow) 0%, #f6f09a 40%, var(--brand-yellow) 85%);
    display: flex; align-items: center; justify-content: center;
  }
  .back-brand { display: flex; align-items: center; gap: 10px; }
  .back-brand .brand-square { width: 38px; height: 38px; }
  .back-brand .brand-name { font-size: 30px; }
  .tagline { font-size: 11px; font-weight: 400; color: var(--ink-soft); letter-spacing: 1.5px; }
</style>
</head>
<body>
<main class="stage">
  <section class="card card-front" aria-label="Business card front">
    <div class="front-edge"></div>
    <div class="front-edge-light"></div>
    <div class="edge-accent"></div>
    <div class="corner-tab"></div>
    <div class="holder">
      <p class="holder-name">MARA QUINLAN</p>
      <p class="holder-role">Graphic Designer</p>
    </div>
    <div class="front-band"></div>
    <div class="front-brand">
      <span class="brand-square"></span>
      <span class="brand-name">BRINDEX</span>
    </div>
    <dl class="contact">
      <dt>Phone</dt><dd>: +41 5550192</dd>
      <dt>Email</dt><dd>: mquinlan@brindex.net</dd>
      <dt>Website</dt><dd>: http://brindex.net/</dd>
      <dt>Address</dt><dd>: 48 Harbour Lane, Eastfield</dd>
    </dl>
  </section>

  <section class="card card-back" aria-label="Business card back">
    <div class="back-brand">
      <span class="brand-square"></span>
      <div>
        <p class="brand-name">BRINDEX</p>
        <p class="tagline">Growing Together</p>
      </div>
    </div>
  </section>
</main>
</body>
</html>
```